Coconut Oil - FOOD Label Design

We have a label design for Coconut oil jars in 2 sizes with stickers for the lids. The bottles are clear, oil is white. Label Size: 217 x 52 mm (Width x Height), Lid ø 50 mm and 268 x 70 mm (Width x Height), Lid ø70 maximum Peel back label is necessary in four languages, engl. in front F, NL, D on the back Brand logo is "velquor". Logo is attached to the AI ​​file We need open Adobe Illustrator files including graphics, photos and fonts. See attached file including all the texts, logos and the cut, with the the cut you can vary as long as you are in the size , hair and body "etc Coconut Oil - FOOD - 200 g to 500 g Responsible Person EAN code - see attached file is in the AI-file

Target Market(s)

european customers

Requirements
Must have
• Velquor logo
Nice to have
• selling points

```html
<!DOCTYPE html>
<html lang="en">
<head>
<meta charset="utf-8">
<title>Velquor Organic Virgin Coconut Oil – Label</title>
<link rel="stylesheet" href="https://fonts.googleapis.com/css2?family=Montserrat:wght@300;400;500;700;800&family=Oswald:wght@400;500&display=swap">
<style>
  :root {
    --bg: #ededed;
    --label: #3b3b3d;
    --white: #ffffff;
    --green: #5cbf2a;
    --green-bright: #62c93a;
    --ink: #1f1f1f;
    --muted: #cfcfcf;
    --photo-warm: #8a6a4c;
    --photo-cool: #5a7a48;
  }
  * { margin: 0; padding: 0; box-sizing: border-box; }
  html, body { width: 1200px; height: 809px; overflow: hidden; background: var(--bg); }
  .canvas { position: relative; width: 1200px; height: 809px; font-family: "Montserrat", sans-serif; }
  .label-shape { position: absolute; inset: 0; }

  .brand { position: absolute; left: 0; width: 1200px; top: 190px; display: flex; flex-direction: column; align-items: center; }
  .brand-dot { width: 58px; height: 58px; border-radius: 50%; background: var(--green); }
  .brand-name { margin-top: 6px; font-weight: 500; font-size: 34px; color: var(--green); letter-spacing: 0.5px; line-height: 1; }

  .product { position: absolute; left: 0; width: 1200px; top: 318px; text-align: center; color: var(--white); }
  .product-kicker { font-weight: 300; font-size: 22px; letter-spacing: 1px; }
  .product-name { font-weight: 700; font-size: 52px; line-height: 1.15; margin-top: 6px; letter-spacing: -0.5px; }
  .product-process { font-weight: 300; font-size: 22px; letter-spacing: 1px; margin-top: 4px; }

  .coconut-photo { position: absolute; left: 512px; top: 468px; width: 176px; height: 96px; border-radius: 8px;
    background: linear-gradient(160deg, var(--photo-warm), var(--photo-cool)); }

  .origin-box { position: absolute; left: 508px; top: 580px; width: 184px; height: 48px; background: var(--green-bright);
    text-align: center; color: var(--ink); }
  .origin-country { font-size: 11px; font-weight: 400; letter-spacing: 0.6px; padding-top: 6px; }
  .origin-volume { font-size: 15px; font-weight: 800; margin-top: 2px; }

  .info-panel { position: absolute; left: 82px; top: 370px; width: 200px; color: var(--muted); font-size: 8.5px; line-height: 1.45; }
  .info-panel p { margin-bottom: 9px; }

  .nutrition { position: absolute; left: 900px; top: 366px; width: 190px; background: var(--white); color: var(--ink);
    font-family: "Oswald", sans-serif; padding: 6px 8px 8px; border: 1px solid #222; }
  .nutrition-title { font-size: 20px; font-weight: 500; line-height: 1; border-bottom: 3px solid var(--ink); padding-bottom: 3px; }
  .nutrition-basis { font-size: 7px; padding: 3px 0; border-bottom: 1px solid var(--ink); }
  .nutrition-row { display: flex; justify-content: space-between; font-size: 11px; padding: 2px 0; border-bottom: 1px solid #555; }
  .nutrition-row:last-child { border-bottom: none; }

  .distributor { position: absolute; left: 900px; top: 578px; color: var(--muted); font-size: 8px; line-height: 1.4; font-style: normal; }
  .distributor-name { font-size: 12px; font-weight: 500; color: var(--white); margin-bottom: 3px; }
</style>
</head>
<body>
<main class="canvas">
  <svg class="label-shape" width="1200" height="809" viewBox="0 0 1200 809" aria-hidden="true">
    <path d="M50,330 H370 Q405,330 425,292 Q475,172 600,172 Q725,172 775,292 Q795,330 830,330 H1150 V650 H50 Z" fill="var(--label)"/>
  </svg>

  <header class="brand">
    <span class="brand-dot"></span>
    <span class="brand-name">velquor</span>
  </header>

  <section class="product">
    <p class="product-kicker">ORGANIC VIRGIN</p>
    <h1 class="product-name">COCONUT OIL</h1>
    <p class="product-process">COLD PROCESSED</p>
  </section>

  <div class="coconut-photo" role="img" aria-label="Photo of halved coconuts resting on green leaves"></div>

  <div class="origin-box">
    <p class="origin-country">PRODUCT OF SRI LANKA</p>
    <p class="origin-volume">℮500 ml</p>
  </div>

  <section class="info-panel">
    <p>Zutaten: Bio-Kokosöl nativ</p>
    <p>Nährwerte je 100 g: Fett 100 g</p>
    <p>Bio-Kokosöl aus frischem Kokosfleisch, ideal zum Braten und Backen.</p>
    <p>Kaltgepresst, ohne Zusätze, mild im Geschmack.</p>
    <p>MHD: siehe Deckel</p>
    <p>Bei Raumtemperatur lagern, vor Licht schützen. Unter 24 °C fest.</p>
  </section>

  <section class="nutrition">
    <h2 class="nutrition-title">NUTRITION FACTS</h2>
    <p class="nutrition-basis">ON THE BASIS PER 100 g</p>
    <div class="nutrition-row"><span>Energy</span><span>3700 kJ / 900 kcal</span></div>
    <div class="nutrition-row"><span>Fat</span><span>100 g</span></div>
    <div class="nutrition-row"><span>Saturated fat</span><span>87 g</span></div>
    <div class="nutrition-row"><span>Protein</span><span>0 g</span></div>
    <div class="nutrition-row"><span>Carbohydrates</span><span>0 g</span></div>
    <div class="nutrition-row"><span>Cholesterol</span><span>0 mg</span></div>
  </section>

  <address class="distributor">
    <p class="distributor-name">Arvenly Foods</p>
    <p>12 Rue des Tilleuls</p>
    <p>69002 Lyon</p>
  </address>
</main>
</body>
</html>
```